UI Improvement for FlorKeep app

We are looking for a talented UI/UX designer to REFINE and enhance the visual design of our mobile application, FlorKeep. The app is fully functional, but we need a designer to improve its aesthetics by specifying design elements such as fonts, colors, spacing, and component styles.
Your task will be to analyze the CURRENT UI and provide detailed design specifications that will make the app more visually appealing, modern, and user-friendly.
TODO:
Review the existing FlorKeep app design (see attachments) and identify areas for visual improvement.
Provide a detailed UI style guide, including:
Typography (font choices, sizes, and weights)
Color palette (primary, secondary, and accent colors)
Component styling (buttons, forms, icons, and interactive elements)
Spacing and layout guidelines (margins, paddings, and alignment)
Ensure the design remains clean, modern, and professional while maintaining usability and accessibility.
Provide design mockups or visual examples (if possible) to illustrate the proposed changes.
Deliverables:
A UI Style Guide (PDF or Figma file) with specifications on fonts, colors, spacing, and UI components.
Optionally, before/after mockups or examples demonstrating the improvements.
Ideal Designer:
Strong experience in mobile UI/UX design.
Understanding of modern design trends and best practices.
Ability to communicate design choices clearly for easy developer implementation.
I have attached 7 images showcasing the main UI screens used in the FlorKeep app. These screens need visual enhancements to improve their overall look and user experience.
The images represent the current design in three key modes:
LIST Mode – Displays data in a structured list format.
READ Mode – Shows detailed information when a user selects an item.
ADD/EDIT Mode – Allows users to input or modify information.
Additionally, there is a ‘MORE’ page, which serves as a menu listing other features of the application.
Task Objective:
Please refine and improve these UIs to create a more modern, visually appealing, and user-friendly experience. Focus on typography, colors, spacing, and component styling to ensure a cohesive and polished design.
Look and feel
Each slider illustrates characteristics of the customer's brand and the style your logo design should communicate.

```html
<!DOCTYPE html>
<html lang="en">
<head>
<meta charset="utf-8">
<title>FlorKeep – Contact &amp; Pilots screens</title>
<link href="https://fonts.googleapis.com/css2?family=Open+Sans:wght@400;600;700;800&display=swap" rel="stylesheet">
<style>
:root{
  --blue:#27a0d4;
  --teal:#1fb49a;
  --canvas:#ececec;
  --panel:#f7f6f8;
  --field:#ffffff;
  --text:#3a3a3a;
  --muted:#8a8a8a;
  --line:#d8d8d8;
  --tint:#e3f3f8;
  --heading:#2a9fce;
}
*{box-sizing:border-box;margin:0;padding:0}
html,body{width:1200px;height:828px;overflow:hidden;background:var(--canvas);font-family:"Open Sans",sans-serif;color:var(--text)}
.screen{position:absolute;background:#fff;overflow:hidden}
.screen--contact-edit{left:25px;top:14px;width:357px;height:772px}
.screen--pilots{left:427px;top:33px;width:345px;height:747px;border-radius:30px}
.screen--contact-read{left:815px;top:21px;width:357px;height:772px}

.header{position:absolute;left:0;top:0;width:100%;background:var(--blue);color:#fff;clip-path:polygon(0 0,100% 0,100% 76%,89% 100%,0 100%)}
.screen--contact-edit .header,.screen--contact-read .header{height:113px}
.screen--pilots .header{height:153px;clip-path:polygon(0 0,100% 0,100% 75%,88% 100%,0 100%)}
.status{position:absolute;left:26px;top:8px;font-size:12px}
.status-icons{position:absolute;right:26px;top:10px;display:flex;gap:5px}
.title{position:absolute;font-weight:800;font-size:28px;letter-spacing:.3px}
.header-actions{position:absolute;display:flex;gap:12px;align-items:center}

.panel{position:absolute;left:26px;width:306px;background:var(--panel);border-radius:8px;padding:10px 11px}
.field{height:33px;background:var(--field);border-radius:17px;box-shadow:0 1px 3px rgba(0,0,0,.12);display:flex;align-items:center;justify-content:space-between;padding:0 16px;font-size:8.5px;margin-bottom:8px}
.field .more{color:#aaa;letter-spacing:1px;font-size:11px}
.required{color:var(--teal);font-size:8.5px;margin:6px 0 4px 12px}
.chev-row{text-align:right;padding:2px 4px 6px;font-size:10px}
.add-icon{width:13px;height:13px;border-radius:50%;background:var(--teal);color:#fff;display:flex;align-items:center;justify-content:center;font-size:12px;font-weight:700;line-height:1}

.nav{position:absolute;left:0;bottom:0;width:100%;height:78px;background:var(--teal);clip-path:polygon(11% 0,100% 0,100% 100%,0 100%,0 50%);display:flex;justify-content:space-around;align-items:flex-end;padding:0 14px 14px 28px}
.nav-item{display:flex;flex-direction:column;align-items:center;gap:5px;color:#fff;font-size:8px}
.nav-item--active{font-weight:700}
.nav-icon{width:22px;height:22px;border-radius:50%;background:#fff;display:flex;align-items:center;justify-content:center}

.search{position:absolute;left:28px;top:84px;width:290px;height:34px;background:#fff;border-radius:17px;display:flex;align-items:center;padding:0 12px;font-size:11px;gap:10px}
.search .advanced{margin-left:auto;color:var(--teal);font-size:8.5px;text-decoration:underline}
.pilot-list{position:absolute;left:0;top:176px;width:100%}
.pilot-row{position:relative;height:68px}
.avatar{position:absolute;width:54px;height:54px;border-radius:50%;background:radial-gradient(circle at 50% 35%,#d9c1a6 0 22%,#f1f4f7 23% 48%,#2b3a55 49%)}
.pilot-row .avatar{left:28px;top:0}
.pilot-name{position:absolute;left:105px;top:12px;font-size:9px;line-height:15px}
.pilot-date{position:absolute;left:258px;top:7px;font-size:9px;display:flex;gap:6px;align-items:center}
.pilot-row::after{content:"";position:absolute;left:100px;right:30px;top:45px;height:1px;background:var(--line)}
.pilot-row--faded{opacity:.4}

.card{position:absolute;left:24px;width:306px;background:var(--tint);border-radius:8px;padding:12px 24px}
.card-title{color:var(--heading);font-weight:700;font-size:14px}
.card-collapse{position:absolute;right:6px;top:11px;color:var(--teal);font-size:8.5px;font-weight:600}
.card-body{font-size:9px;line-height:18px;margin-top:8px}
.card-rule{height:2px;background:#fff;margin-top:8px;margin-left:0}
</style>
</head>
<body>

<!-- Contact – edit mode -->
<section class="screen screen--contact-edit">
  <header class="header">
    <span class="status">9:30</span>
    <span class="status-icons">
      <svg width="14" height="9"><rect x="0" y="6" width="2" height="3" fill="#fff"/><rect x="4" y="4" width="2" height="5" fill="#fff"/><rect x="8" y="2" width="2" height="7" fill="#fff"/><rect x="12" y="0" width="2" height="9" fill="#fff"/></svg>
      <svg width="13" height="9"><path d="M1 3a8 8 0 0 1 11 0M3 5.5a5 5 0 0 1 7 0" stroke="#fff" stroke-width="1.4" fill="none"/><circle cx="6.5" cy="8" r="1.2" fill="#fff"/></svg>
      <svg width="20" height="9"><rect x=".5" y=".5" width="17" height="8" rx="2" stroke="#fff" fill="none"/><rect x="2" y="2" width="14" height="5" fill="#fff"/><rect x="18.5" y="3" width="1.5" height="3" fill="#fff"/></svg>
    </span>
    <h1 class="title" style="left:26px;top:58px">Contact</h1>
    <div class="header-actions" style="right:26px;top:68px">
      <svg width="12" height="16"><path d="M0 0h12v16l-6-5-6 5z" fill="#fff"/></svg>
      <svg width="22" height="5"><circle cx="2.5" cy="2.5" r="2.3" fill="#fff"/><circle cx="11" cy="2.5" r="2.3" fill="#fff"/><circle cx="19.5" cy="2.5" r="2.3" fill="#fff"/></svg>
    </div>
  </header>

  <div class="panel" style="top:130px;height:206px">
    <div class="field">Business Name -e<span class="more">•••</span></div>
    <div class="field">First Name - e</div>
    <div class="field">Middle Name - e</div>
    <div class="field">Last Name - e</div>
  </div>

  <div class="panel" style="top:345px;height:325px">
    <div class="chev-row"><svg width="8" height="5"><path d="M1 4.5L4 1.5 7 4.5" stroke="#333" fill="none" stroke-width="1.2"/></svg></div>
    <div class="field">Address Lable Tag -e<span class="more">•••</span></div>
    <div class="required">Required</div>
    <div class="field">AddressLine 1 -e</div>
    <div class="required">Required</div>
    <div class="field">AddressLine 2 -e</div>
    <div class="field" style="margin-top:10px">Address City<svg width="7" height="12"><path d="M3.5 0L7 5H0zM3.5 12L0 7h7z" fill="#aaa"/></svg></div>
    <div class="field">Address State</div>
    <div class="field">Zip - e</div>
  </div>

  <nav class="nav">
    <div class="nav-item nav-item--active"><span class="nav-icon"><svg width="12" height="12"><circle cx="6" cy="3.5" r="3" fill="#1fb49a"/><path d="M0 12a6 5 0 0 1 12 0z" fill="#1fb49a"/></svg></span>Contact</div>
    <div class="nav-item"><span class="nav-icon"><svg width="12" height="12"><rect x="2" y="0" width="8" height="3" rx="1" fill="#1fb49a"/><circle cx="6" cy="5" r="2.5" fill="#1fb49a"/><path d="M0 12a6 5 0 0 1 12 0z" fill="#1fb49a"/></svg></span>Pilot</div>
    <div class="nav-item"><span class="nav-icon"><svg width="14" height="14"><path d="M7 0c1 0 1 1 1 2v3l6 3v1.5L8 8v3l2 1.5V14L7 13 4 14v-1.5L6 11V8L0 9.5V8l6-3V2c0-1 0-2 1-2z" fill="#1fb49a"/></svg></span>Plane</div>
    <div class="nav-item"><span class="nav-icon" style="background:none"><svg width="20" height="18"><circle cx="6" cy="6" r="3.5" fill="#fff"/><path d="M0 17a6 6 0 0 1 12 0z" fill="#fff"/><circle cx="14" cy="5" r="5" fill="#fff"/><text x="14" y="8" font-size="8" font-weight="700" text-anchor="middle" fill="#1fb49a" font-family="Open Sans">?</text></svg></span>Fit Request</div>
    <div class="nav-item"><span class="nav-icon"><svg width="12" height="3"><circle cx="1.5" cy="1.5" r="1.5" fill="#1fb49a"/><circle cx="6" cy="1.5" r="1.5" fill="#1fb49a"/><circle cx="10.5" cy="1.5" r="1.5" fill="#1fb49a"/></svg></span>More...</div>
  </nav>
</section>

<!-- Pilots – list mode -->
<section class="screen screen--pilots">
  <header class="header">
    <span class="status" style="left:33px;top:14px">9:30</span>
    <span class="status-icons" style="top:16px;right:14px">
      <svg width="14" height="9"><rect x="0" y="6" width="2" height="3" fill="#fff"/><rect x="4" y="4" width="2" height="5" fill="#fff"/><rect x="8" y="2" width="2" height="7" fill="#fff"/><rect x="12" y="0" width="2" height="9" fill="#fff"/></svg>
      <svg width="13" height="9"><path d="M1 3a8 8 0 0 1 11 0M3 5.5a5 5 0 0 1 7 0" stroke="#fff" stroke-width="1.4" fill="none"/><circle cx="6.5" cy="8" r="1.2" fill="#fff"/></svg>
      <svg width="20" height="9"><rect x=".5" y=".5" width="17" height="8" rx="2" stroke="#fff" fill="none"/><rect x="2" y="2" width="14" height="5" fill="#fff"/><rect x="18.5" y="3" width="1.5" height="3" fill="#fff"/></svg>
    </span>
    <h1 class="title" style="left:28px;top:32px">Pilots</h1>
    <div class="header-actions" style="right:26px;top:42px">
      <svg width="14" height="14"><circle cx="7" cy="7" r="7" fill="#fff"/><path d="M7 3.5v7M3.5 7h7" stroke="#27a0d4" stroke-width="1.8"/></svg>
      <svg width="22" height="5"><circle cx="2.5" cy="2.5" r="2.3" fill="#fff"/><circle cx="11" cy="2.5" r="2.3" fill="#fff"/><circle cx="19.5" cy="2.5" r="2.3" fill="#fff"/></svg>
    </div>
    <div class="search" style="left:28px;top:80px">
      <svg width="15" height="15"><circle cx="6" cy="6" r="5" stroke="#777" stroke-width="1.3" fill="none"/><path d="M10 10l4 4" stroke="#777" stroke-width="1.3"/></svg>
      <span style="color:#444">Search</span>
      <span class="advanced">Advanced Search</span>
    </div>
  </header>

  <div class="pilot-list" style="top:180px">
    <div class="pilot-row"><div class="avatar" role="img" aria-label="Pilot portrait photo"></div><div class="pilot-name">Alder, Corwin, Blake, 3<br>182133,</div><div class="pilot-date"><svg width="12" height="12"><rect x=".5" y="1.5" width="11" height="10" fill="none" stroke="#999"/><path d="M.5 4h11M3 6h6M3 8.5h6" stroke="#999"/></svg>9/30/24</div></div>
    <div class="pilot-row"><div class="avatar" role="img" aria-label="Pilot portrait photo"></div><div class="pilot-name">Bellamy, Rowan<br>4467155</div><div class="pilot-date"><svg width="12" height="12"><rect x=".5" y="1.5" width="11" height="10" fill="none" stroke="#999"/><path d="M.5 4h11M3 6h6M3 8.5h6" stroke="#999"/></svg>2/28/25</div></div>
    <div class="pilot-row"><div class="avatar" role="img" aria-label="Pilot portrait photo"></div><div class="pilot-name">Brennick, Alton<br>2663187</div><div class="pilot-date"><svg width="12" height="12"><rect x=".5" y="1.5" width="11" height="10" fill="none" stroke="#999"/><path d="M.5 4h11M3 6h6M3 8.5h6" stroke="#999"/></svg>10/30/24</div></div>
    <div class="pilot-row"><div class="avatar" role="img" aria-label="Pilot portrait photo"></div><div class="pilot-name">Corva, Ada, Silas<br>4360575</div><div class="pilot-date"><svg width="12" height="12"><rect x=".5" y="1.5" width="11" height="10" fill="none" stroke="#999"/><path d="M.5 4h11M3 6h6M3 8.5h6" stroke="#999"/></svg>3/30/25,</div></div>
    <div class="pilot-row"><div class="avatar" role="img" aria-label="Pilot portrait photo"></div><div class="pilot-name">Cato Granger,<br>182133,</div><div class="pilot-date"><svg width="12" height="12"><rect x=".5" y="1.5" width="11" height="10" fill="none" stroke="#999"/><path d="M.5 4h11M3 6h6M3 8.5h6" stroke="#999"/></svg>9/30/24</div></div>
    <div class="pilot-row"><div class="avatar" role="img" aria-label="Pilot portrait photo"></div><div class="pilot-name">Garrow, Colby,<br>3423819</div><div class="pilot-date"><svg width="12" height="12"><rect x=".5" y="1.5" width="11" height="10" fill="none" stroke="#999"/><path d="M.5 4h11M3 6h6M3 8.5h6" stroke="#999"/></svg>2/28/25,</div></div>
    <div class="pilot-row"><div class="avatar" role="img" aria-label="Pilot portrait photo"></div><div class="pilot-name">Gable, Jonah, Ames<br>2761635</div><div class="pilot-date"><svg width="12" height="12"><rect x=".5" y="1.5" width="11" height="10" fill="none" stroke="#999"/><path d="M.5 4h11M3 6h6M3 8.5h6" stroke="#999"/></svg>3/6/23</div></div>
    <div class="pilot-row pilot-row--faded"><div class="avatar" role="img" aria-label="Pilot portrait photo"></div><div class="pilot-name">Gable, Jonah, Ames<br>2761635</div><div class="pilot-date"><svg width="12" height="12"><rect x=".5" y="1.5" width="11" height="10" fill="none" stroke="#999"/><path d="M.5 4h11M3 6h6M3 8.5h6" stroke="#999"/></svg>3/6/23</div></div>
  </div>

  <nav class="nav" style="height:72px;padding-bottom:12px">
    <div class="nav-item"><span class="nav-icon"><svg width="12" height="12"><circle cx="6" cy="3.5" r="3" fill="#1fb49a"/><path d="M0 12a6 5 0 0 1 12 0z" fill="#1fb49a"/></svg></span>Contact</div>
    <div class="nav-item nav-item--active"><span class="nav-icon"><svg width="12" height="12"><rect x="2" y="0" width="8" height="3" rx="1" fill="#1fb49a"/><circle cx="6" cy="5" r="2.5" fill="#1fb49a"/><path d="M0 12a6 5 0 0 1 12 0z" fill="#1fb49a"/></svg></span>Pilot</div>
    <div class="nav-item"><span class="nav-icon"><svg width="14" height="14"><path d="M7 0c1 0 1 1 1 2v3l6 3v1.5L8 8v3l2 1.5V14L7 13 4 14v-1.5L6 11V8L0 9.5V8l6-3V2c0-1 0-2 1-2z" fill="#1fb49a"/></svg></span>Plane</div>
    <div class="nav-item"><span class="nav-icon" style="background:none"><svg width="20" height="18"><circle cx="6" cy="6" r="3.5" fill="#fff"/><path d="M0 17a6 6 0 0 1 12 0z" fill="#fff"/><circle cx="14" cy="5" r="5" fill="#fff"/><text x="14" y="8" font-size="8" font-weight="700" text-anchor="middle" fill="#1fb49a" font-family="Open Sans">?</text></svg></span>Fit Request</div>
    <div class="nav-item"><span class="nav-icon"><svg width="12" height="3"><circle cx="1.5" cy="1.5" r="1.5" fill="#1fb49a"/><circle cx="6" cy="1.5" r="1.5" fill="#1fb49a"/><circle cx="10.5" cy="1.5" r="1.5" fill="#1fb49a"/></svg></span>More...</div>
  </nav>
</section>

<!-- Contact – read mode -->
<section class="screen screen--contact-read">
  <header class="header">
    <span class="status">9:30</span>
    <span class="status-icons">
      <svg width="14" height="9"><rect x="0" y="6" width="2" height="3" fill="#fff"/><rect x="4" y="4" width="2" height="5" fill="#fff"/><rect x="8" y="2" width="2" height="7" fill="#fff"/><rect x="12" y="0" width="2" height="9" fill="#fff"/></svg>
      <svg width="13" height="9"><path d="M1 3a8 8 0 0 1 11 0M3 5.5a5 5 0 0 1 7 0" stroke="#fff" stroke-width="1.4" fill="none"/><circle cx="6.5" cy="8" r="1.2" fill="#fff"/></svg>
      <svg width="20" height="9"><rect x=".5" y=".5" width="17" height="8" rx="2" stroke="#fff" fill="none"/><rect x="2" y="2" width="14" height="5" fill="#fff"/><rect x="18.5" y="3" width="1.5" height="3" fill="#fff"/></svg>
    </span>
    <svg style="position:absolute;left:26px;top:62px" width="22" height="14"><path d="M21 7H2M8 1L2 7l6 6" stroke="#fff" stroke-width="1.6" fill="none"/></svg>
    <h1 class="title" style="left:0;right:0;text-align:center;top:52px">Contact</h1>
    <div class="header-actions" style="right:26px;top:60px">
      <svg width="22" height="5"><circle cx="2.5" cy="2.5" r="2.3" fill="#fff"/><circle cx="11" cy="2.5" r="2.3" fill="#fff"/><circle cx="19.5" cy="2.5" r="2.3" fill="#fff"/></svg>
    </div>
  </header>

  <div class="panel" style="top:130px;height:319px">
    <div class="field" style="margin-bottom:7px">Add Email -e<span class="add-icon">+</span></div>
    <div class="field" style="margin-bottom:7px">Add Social Media - e<span class="add-icon">+</span></div>
    <div class="field" style="margin-bottom:7px">Add Emergency Contact- e<span class="add-icon">+</span></div>
    <div class="field" style="margin-bottom:7px">Add Personal Information- e<span class="add-icon">+</span></div>
    <div class="field" style="margin-bottom:7px">Add Work Info- e<span class="add-icon">+</span></div>
    <div class="field" style="margin-bottom:7px">Add Skills / Talents - e<span class="add-icon">+</span></div>
    <div class="field" style="margin-bottom:7px">Add Resources - e<span class="add-icon">+</span></div>
  </div>

  <div class="card" style="top:459px;height:112px">
    <div class="card-title">Pilots -e</div>
    <span class="card-collapse">Collapse</span>
    <div style="position:relative;height:52px;margin-top:6px">
      <div class="avatar" role="img" aria-label="Pilot portrait photo" style="left:-6px;top:0;width:44px;height:44px"></div>
      <div class="pilot-name" style="left:52px;top:6px">Ashford, Clive<br>3647946</div>
      <div class="pilot-date" style="left:180px;top:4px"><svg width="12" height="12"><rect x=".5" y="1.5" width="11" height="10" fill="none" stroke="#999"/><path d="M.5 4h11M3 6h6M3 8.5h6" stroke="#999"/></svg>10/31/23</div>
      <svg style="position:absolute;right:-14px;top:6px" width="9" height="6"><path d="M1 1l3.5 3.5L8 1" stroke="#333" fill="none" stroke-width="1.2"/></svg>
    </div>
    <div class="card-rule" style="margin-top:0"></div>
  </div>

  <div class="card" style="top:583px;height:93px">
    <div class="card-title">Aircraft Owner -e</div>
    <span class="card-collapse">Collapse</span>
    <div class="card-body" style="margin-top:2px">Personal: Ashford, Clive: Skyline: 182T: Skyline Aircraft Company, Single Engine, 1100</div>
    <div class="card-rule" style="margin-top:4px"></div>
  </div>

  <nav class="nav">
    <div class="nav-item nav-item--active"><span class="nav-icon"><svg width="12" height="12"><circle cx="6" cy="3.5" r="3" fill="#1fb49a"/><path d="M0 12a6 5 0 0 1 12 0z" fill="#1fb49a"/></svg></span>Contact</div>
    <div class="nav-item"><span class="nav-icon"><svg width="12" height="12"><rect x="2" y="0" width="8" height="3" rx="1" fill="#1fb49a"/><circle cx="6" cy="5" r="2.5" fill="#1fb49a"/><path d="M0 12a6 5 0 0 1 12 0z" fill="#1fb49a"/></svg></span>Pilot</div>
    <div class="nav-item"><span class="nav-icon"><svg width="14" height="14"><path d="M7 0c1 0 1 1 1 2v3l6 3v1.5L8 8v3l2 1.5V14L7 13 4 14v-1.5L6 11V8L0 9.5V8l6-3V2c0-1 0-2 1-2z" fill="#1fb49a"/></svg></span>Plane</div>
    <div class="nav-item"><span class="nav-icon" style="background:none"><svg width="20" height="18"><circle cx="6" cy="6" r="3.5" fill="#fff"/><path d="M0 17a6 6 0 0 1 12 0z" fill="#fff"/><circle cx="14" cy="5" r="5" fill="#fff"/><text x="14" y="8" font-size="8" font-weight="700" text-anchor="middle" fill="#1fb49a" font-family="Open Sans">?</text></svg></span>Fit Request</div>
    <div class="nav-item"><span class="nav-icon"><svg width="12" height="3"><circle cx="1.5" cy="1.5" r="1.5" fill="#1fb49a"/><circle cx="6" cy="1.5" r="1.5" fill="#1fb49a"/><circle cx="10.5" cy="1.5" r="1.5" fill="#1fb49a"/></svg></span>More...</div>
  </nav>
</section>

</body>
</html>
```